Business Card Design Project

We need a Business Card for an Mechanical Engineering firm in Singapore. The design should be Modern & Technical looking, yet eye catching.

Our company deals in Cutting Tools & Machine Accessories for the Manufacturing Industries such as Oil & Gas, Aero Space, etc... For more information on our Company, you can either email me or view our website www.torvalen.com.sg.

We are trying to revamp our image to give our consumers a fresh new perspective to our company, so we welcome all ideas.

Industry/Entity Type

Business

Requirements
Must have
• Must incorporate New Company Logo into the card as shown in Uploaded file.

```html
<!DOCTYPE html>
<html lang="en">
<head>
<meta charset="utf-8">
<title>Torvalen Tools – Business Card</title>
<link href="https://fonts.googleapis.com/css2?family=Open+Sans:ital,wght@0,400;0,600;1,400&display=swap" rel="stylesheet">
<style>
  :root {
    --backdrop: #e4e4e2;
    --card: #ffffff;
    --card-shade: #f1f1f1;
    --brand-red: #9c1c24;
    --brand-red-dark: #6e1218;
    --ink: #2a2a2a;
    --ink-soft: #4a4a4a;
    --rule: #d6d6d6;
  }
  * { box-sizing: border-box; margin: 0; padding: 0; }
  html, body { width: 1200px; height: 944px; overflow: hidden; }
  body {
    background: var(--backdrop);
    font-family: "Open Sans", Arial, sans-serif;
    color: var(--ink);
    position: relative;
  }
  .card {
    position: absolute;
    width: 620px;
    height: 360px;
    border-radius: 22px;
    background: linear-gradient(180deg, var(--card) 0%, var(--card) 70%, var(--card-shade) 100%);
    box-shadow: 0 8px 24px rgba(0,0,0,0.18);
    overflow: hidden;
  }
  .card::after {
    content: "";
    position: absolute;
    left: 0; right: 0; bottom: 0;
    height: 22px;
    background: linear-gradient(180deg, var(--brand-red) 0%, var(--brand-red-dark) 100%);
  }
  .card--front { left: 70px; top: 70px; }
  .card--back { left: 510px; top: 500px; }

  .brand {
    display: flex;
    align-items: center;
    gap: 14px;
    color: var(--brand-red);
    font-weight: 600;
    letter-spacing: 1px;
    text-transform: uppercase;
    white-space: nowrap;
  }
  .brand__dot {
    width: 22px; height: 22px;
    border-radius: 50%;
    background: var(--brand-red);
    flex: none;
  }

  .card--front .brand {
    position: absolute;
    left: 0; right: 0; top: 125px;
    justify-content: center;
    font-size: 44px;
  }
  .card--front .website {
    position: absolute;
    left: 0; right: 0; top: 218px;
    text-align: center;
    font-size: 21px;
    letter-spacing: 0.5px;
    color: var(--ink);
  }

  .card--back .brand {
    position: absolute;
    left: 34px; top: 150px;
    font-size: 27px;
    gap: 10px;
  }
  .card--back .brand__dot { width: 16px; height: 16px; }
  .divider {
    position: absolute;
    left: 338px; top: 40px;
    width: 1px; height: 270px;
    background: var(--rule);
  }
  .contact {
    position: absolute;
    left: 362px; top: 52px;
    right: 20px;
  }
  .contact__name { font-size: 22px; color: var(--ink); }
  .contact__role { font-size: 17px; font-style: italic; color: var(--brand-red); margin-bottom: 26px; }
  .contact__list { list-style: none; font-size: 17px; color: var(--ink-soft); line-height: 1.3; }
  .contact__item { display: flex; align-items: flex-start; gap: 10px; margin-bottom: 2px; }
  .contact__item svg { width: 14px; height: 14px; margin-top: 4px; flex: none; fill: var(--brand-red); }
  .contact__item .accent { color: var(--brand-red); }
</style>
</head>
<body>
  <section class="card card--front" aria-label="Business card front">
    <div class="brand"><span class="brand__dot"></span>Torvalen Tools</div>
    <p class="website">www.torvalentools.com</p>
  </section>

  <section class="card card--back" aria-label="Business card back">
    <div class="brand"><span class="brand__dot"></span>Torvalen Tools</div>
    <div class="divider"></div>
    <div class="contact">
      <p class="contact__name">Marcus Ellery</p>
      <p class="contact__role">manager</p>
      <ul class="contact__list">
        <li class="contact__item">
          <svg viewBox="0 0 14 14" aria-hidden="true"><path d="M7 1 L13 6.5 H11 V13 H8.5 V9 H5.5 V13 H3 V6.5 H1 Z"/></svg>
          <span>48 Kallang Bahru Rd.<br>Singapore 339334</span>
        </li>
        <li class="contact__item">
          <svg viewBox="0 0 14 14" aria-hidden="true"><path d="M3 1 L5.5 1 L6.5 4 L5 5.2 C5.8 7 7 8.2 8.8 9 L10 7.5 L13 8.5 L13 11 C13 12 12 13 11 13 C5.5 12.5 1.5 8.5 1 3 C1 2 2 1 3 1 Z"/></svg>
          <span>6741-2080</span>
        </li>
        <li class="contact__item">
          <svg viewBox="0 0 14 14" aria-hidden="true"><rect x="2" y="1" width="10" height="12" rx="1.5"/></svg>
          <span>6741-2081</span>
        </li>
        <li class="contact__item">
          <svg viewBox="0 0 14 14" aria-hidden="true"><path d="M1 3 H13 V11 H1 Z M1 3 L7 8 L13 3" /></svg>
          <span>info@torvalentools.com</span>
        </li>
        <li class="contact__item">
          <svg viewBox="0 0 14 14" aria-hidden="true"><circle cx="7" cy="7" r="6"/></svg>
          <span>www.<span class="accent">torvalentools</span>.com</span>
        </li>
      </ul>
    </div>
  </section>
</body>
</html>
```